Coffee and Plastics

I am looking for a completely new site that shows the products we have. Our current site is www.velmorebrothersbeans.com. We are open minded to what designers come up with. Our current site is www.velmorebrothersbeans.com. You can you the information from there to start the site. I need these tabs on the main home page. ( Home, Coffee & Tea, Condiments, and Paper and Plastics, and Contact.) You can take photos and info from my Current site. In products page.
I will be uploading info and photo for paper and plastics.
Look and feel
Each slider illustrates characteristics of the customer's brand and the style your logo design should communicate.

```html
<!DOCTYPE html>
<html lang="en">
<head>
<meta charset="utf-8">
<title>Velmore Brothers Beans</title>
<link rel="stylesheet" href="https://fonts.googleapis.com/css2?family=Cinzel:wght@700&family=Marcellus+SC&family=Open+Sans:ital,wght@0,400;0,600;0,700;1,400;1,700&family=Raleway:wght@400;500;600&display=swap">
<style>
:root{
  --paper:#ece8dc;
  --paper-dark:#e3ddcd;
  --ink:#2a211b;
  --brown:#4a1d12;
  --brown-deep:#3a150d;
  --nav:#2b261c;
  --nav-grey:#5f5f58;
  --red:#e0353a;
  --muted:#5a5550;
  --line:#cfc8b8;
  --tan:#a99b86;
  --teal:#2f9bb0;
  --white:#ffffff;
}
*{box-sizing:border-box;margin:0;padding:0}
html,body{width:833px;height:1200px;overflow:hidden;background:var(--paper)}
body{font-family:"Open Sans",sans-serif;color:var(--ink)}
.page{position:relative;width:833px;height:1200px;overflow:hidden;background:var(--paper);border-top:2px solid #d8d2c3}
.abs{position:absolute}
.dash{position:absolute;height:0;border-top:1px dashed var(--line)}

/* brand */
.brand{left:120px;top:40px;width:132px;height:110px;display:flex;flex-direction:column;align-items:center;justify-content:center;gap:8px}
.brand-mark{width:22px;height:22px;background:var(--brown)}
.brand-name{font-family:"Raleway",sans-serif;font-weight:600;font-size:17px;line-height:1.15;color:var(--brown);text-align:center}

/* top bar */
.topbar{left:298px;top:12px;width:416px;height:41px;background:var(--white)}
.call{left:10px;top:11px;font-family:"Marcellus SC",serif;font-size:15px;color:var(--ink)}
.call span{font-family:"Open Sans",sans-serif;font-size:11px;color:var(--red)}
.search{left:248px;top:13px;width:152px;height:15px;background:#e2e0dc;font-size:7px;color:#9a968f;padding:3px 6px}
.search svg{position:absolute;right:5px;top:3px}

.welcome{left:298px;top:79px;width:416px;text-align:center}
.welcome h1{font-family:"Marcellus SC",serif;font-weight:400;font-size:19px;letter-spacing:.5px;color:var(--ink);white-space:nowrap}
.welcome p{margin-top:8px;font-size:7.5px;line-height:11.5px;color:var(--muted);padding:0 12px}

/* nav */
.nav{left:118px;top:196px;width:138px;list-style:none}
.nav li{height:23px;margin-bottom:6px;background:var(--nav);color:var(--white);font-family:"Raleway",sans-serif;font-weight:500;font-size:10.5px;display:flex;align-items:center;justify-content:center;clip-path:polygon(1% 0,100% 4%,98% 100%,0 96%)}
.nav li:nth-child(2){clip-path:polygon(0 6%,99% 0,100% 96%,1% 100%)}
.nav li:nth-child(3){clip-path:polygon(0 0,97% 6%,95% 100%,2% 94%)}
.nav li.active{background:var(--nav-grey);font-family:"Open Sans",sans-serif;font-weight:700;height:25px}
.best{left:118px;top:390px;width:135px;height:40px;background:var(--red);color:var(--white);font-style:italic;font-weight:700;font-size:14px;display:flex;align-items:center;justify-content:center;clip-path:polygon(0 0,100% 3%,99% 100%,0 97%)}

/* slider */
.slider{left:298px;top:186px;width:413px;height:244px;background:var(--white);box-shadow:0 6px 8px -4px rgba(0,0,0,.25)}
.slide-photo{position:absolute;left:4px;top:4px;width:405px;height:236px;background:radial-gradient(ellipse at 60% 40%,#c5ad8a,#a88d68 70%,#94795a)}
.slide-text{left:162px;top:70px;width:240px}
.slide-text h2{font-family:"Raleway",sans-serif;font-weight:400;font-size:21px;line-height:26px;color:var(--brown-deep);white-space:nowrap}
.slide-text p{font-family:"Raleway",sans-serif;font-size:10.5px;line-height:13px;color:var(--ink);margin-top:4px}
.btn-read{display:inline-block;margin-top:8px;background:var(--brown-deep);color:var(--white);font-family:"Raleway",sans-serif;font-size:9.5px;padding:4px 20px}
.dots{display:flex;gap:4px;margin-top:14px}
.dots i{width:8px;height:8px;border-radius:50%;border:1px solid #6e5a44;background:#d8cbb8}
.dots i:first-child{background:var(--brown-deep)}

/* products */
.products{left:121px;top:490px;display:flex;gap:8px}
.product{position:relative;width:111px;height:123px;background:#1d1c1e}
.product-photo{position:absolute;left:10px;top:8px;width:91px;height:66px;background:radial-gradient(ellipse,#d9d9d9,#8d8d8d 60%,#1d1c1e 80%)}
.product h3{position:absolute;left:6px;top:88px;font-family:"Cinzel",serif;font-size:11px;color:var(--red)}
.product-meta{position:absolute;left:7px;right:7px;top:106px;display:flex;justify-content:space-between;font-family:"Marcellus SC",serif;font-size:8px;color:#c7c2b8}
.track{left:120px;top:620px;width:590px;height:4px;background:#d6d0c2;border-radius:2px}
.thumb{left:70px;top:0;width:90px;height:4px;background:var(--red);border-radius:2px}

/* promo */
.promo{left:120px;top:652px;width:590px;height:216px;background:var(--paper-dark)}
.promo-copy{left:22px;top:33px;width:340px}
.promo-copy .kicker{font-family:"Marcellus SC",serif;font-size:15px;color:var(--ink)}
.promo-copy h2{font-family:"Marcellus SC",serif;font-weight:400;font-size:21px;line-height:26px;color:var(--ink);margin-top:1px;white-space:nowrap}
.promo-copy p{font-size:7.5px;line-height:11.5px;color:var(--muted);margin-top:10px;width:256px}
.btn-off{left:22px;top:150px;width:152px;height:36px;background:var(--tan);color:var(--white);font-family:"Raleway",sans-serif;font-weight:500;font-size:16px;display:flex;align-items:center;justify-content:center;box-shadow:0 2px 0 #8e826f}
.promo-photo{left:358px;top:14px;width:190px;height:190px;background:radial-gradient(ellipse at 50% 45%,#cfc4ac,#a79a80 55%,rgba(227,221,205,0) 72%)}

/* cards */
.card{top:906px;width:291px;height:73px;border:3px solid var(--white);box-shadow:0 1px 3px rgba(0,0,0,.2);overflow:hidden}
.card-light{left:121px;background:#f3f1ef}
.card-teal{left:422px;background:linear-gradient(180deg,#36a4b8 0%,#2b90a3 70%,#3f4447 72%,#2f3234 100%)}
.card-photo{position:absolute;left:184px;top:4px;width:93px;height:62px;background:radial-gradient(ellipse,#a48466,#c8b49c 60%,#f3f1ef 80%)}
.card h3{position:absolute;left:12px;top:8px;font-family:"Raleway",sans-serif;font-weight:400;font-size:15px;color:var(--ink)}
.card p{position:absolute;left:12px;top:30px;width:165px;font-size:7px;line-height:9.5px;color:var(--muted)}
.card .more{position:absolute;left:12px;top:55px;font-size:7px;color:var(--red);display:flex;align-items:center;gap:4px}
.card-teal h3,.card-teal p,.card-teal .more{color:var(--ink)}
.card-teal .more{color:var(--white)}
.card-teal .cup{position:absolute;right:26px;top:6px;width:40px;height:62px;background:linear-gradient(90deg,#dcdcdc,#ffffff 50%,#d4d4d4)}

/* footer */
.fcol{top:1052px}
.fcol h4{font-family:"Raleway",sans-serif;font-weight:500;font-size:13px;color:var(--ink);display:flex;align-items:center;gap:6px}
.fcol h4 .sq{width:8px;height:8px;background:var(--red)}
.contact-item{position:absolute;left:0;display:flex;gap:8px;font-size:6.5px;line-height:9px;color:var(--muted);white-space:nowrap}
.ico{width:16px;height:16px;background:var(--brown-deep);display:flex;align-items:center;justify-content:center;flex:none}
.post{font-size:6.5px;line-height:9px;color:var(--muted);width:112px}
.post em{display:block;color:var(--ink)}
.field{width:141px;height:15px;background:var(--white);border:1px solid #b9b3a7;font-style:italic;font-size:6.5px;color:#555;padding:3px 6px;margin-top:6px}
.signup{display:inline-block;margin-top:6px;background:var(--brown-deep);color:var(--white);font-size:7.5px;padding:3px 9px}
.foot{left:0;top:1178px;width:833px;height:22px;background:var(--brown-deep);color:#e6ddd4;font-size:6.5px;display:flex;align-items:center;justify-content:center}
</style>
</head>
<body>
<div class="page">

  <div class="abs brand">
    <div class="brand-mark"></div>
    <div class="brand-name">Velmore<br>Brothers Beans</div>
  </div>

  <div class="abs topbar">
    <div class="abs call">Call us : <span>0800 555 018 246</span></div>
    <div class="abs search">Search...
      <svg width="8" height="8" viewBox="0 0 10 10"><circle cx="4" cy="4" r="3" fill="none" stroke="#8b8780" stroke-width="1.4"/><line x1="6.3" y1="6.3" x2="9.3" y2="9.3" stroke="#8b8780" stroke-width="1.6"/></svg>
    </div>
  </div>
  <div class="dash" style="left:298px;top:66px;width:416px"></div>

  <div class="abs welcome">
    <h1>Welcome to the Velmore Brothers Beans</h1>
    <p>Sed ut perspiciatis unde omnis iste natus error sit totam rem aperiam, eaque ipsa quae ab illo inventore veritatis et quasi architecto beatae vitae dicta sunt expli Nemo enim ipsam sit aspernatur aut odit aut fugit, sed quiamagni dolores eos qui ratione voluptatem sequi nesciunt.</p>
  </div>
  <div class="dash" style="left:298px;top:166px;width:416px"></div>

  <ul class="abs nav">
    <li>Home</li>
    <li>Coffee &amp; Tea</li>
    <li>Condiments</li>
    <li>Paper</li>
    <li>Plastics</li>
    <li class="active">CONTACT</li>
  </ul>
  <div class="dash" style="left:120px;top:376px;width:134px"></div>
  <div class="abs best">Best Coffee Cup</div>

  <div class="abs slider">
    <div class="slide-photo" role="img" aria-label="Takeaway coffee cup with cardboard sleeve on burlap"></div>
    <div class="abs slide-text">
      <h2>Velmore Brothers Beans</h2>
      <p>Lorem ipsum dolor sit amet elit, sed do eiusmod tempor incididunt ut labore et dolore Ut enim</p>
      <span class="btn-read">Read More</span>
      <div class="dots"><i></i><i></i><i></i><i></i></div>
    </div>
  </div>

  <div class="dash" style="left:120px;top:468px;width:590px"></div>

  <div class="abs products">
    <div class="product"><div class="product-photo" role="img" aria-label="Clear compartment food tray"></div><h3>Sitw kia</h3><div class="product-meta"><span>Add to Cart</span><span>$0.00</span></div></div>
    <div class="product"><div class="product-photo" role="img" aria-label="White plastic compartment plate"></div><h3>Lipsum</h3><div class="product-meta"><span>Add to Cart</span><span>$0.00</span></div></div>
    <div class="product"><div class="product-photo" role="img" aria-label="Round clear sectioned platter"></div><h3>Sitquet</h3><div class="product-meta"><span>Add to Cart</span><span>$0.00</span></div></div>
    <div class="product"><div class="product-photo" role="img" aria-label="White foam divided tray"></div><h3>Eiusmod</h3><div class="product-meta"><span>Add to Cart</span><span>$0.00</span></div></div>
    <div class="product"><div class="product-photo" role="img" aria-label="Cup lid beside paper coffee cup"></div><h3>Eiusmod</h3><div class="product-meta"><span>Add to Cart</span><span>$0.00</span></div></div>
  </div>
  <div class="abs track"><div class="abs thumb"></div></div>

  <div class="dash" style="left:120px;top:651px;width:590px"></div>
  <div class="abs promo">
    <div class="abs promo-copy">
      <div class="kicker">The Best Coffee Cup</div>
      <h2>At Velmore Brothers Beans</h2>
      <p>Sed ut perspiciatis unde omnis iste natus error sit voluptatem accusantium doloremque laudantium, totam rem aperiam, eaque ipsa quae ab illo inventore veritatis et quasi architecto beatae vitae dicta sunt explicabo. Nemo enim ipsam .</p>
    </div>
    <div class="abs btn-off">Get 15 % Off</div>
    <div class="abs promo-photo" role="img" aria-label="Three takeaway coffee cups with sleeves"></div>
  </div>
  <div class="dash" style="left:120px;top:868px;width:590px"></div>

  <div class="abs card card-light">
    <div class="card-photo" role="img" aria-label="Two coffee cups in a cardboard carrier"></div>
    <h3>Lorem ipsum dolor</h3>
    <p>sit amet, consectetur adipisicing elit, sed do eiusmod tempor incididunt ut labore et dolore</p>
    <div class="more">Read more <svg width="16" height="4" viewBox="0 0 16 4"><line x1="0" y1="2" x2="14" y2="2" stroke="currentColor"/><path d="M12 0 L16 2 L12 4Z" fill="currentColor"/></svg></div>
  </div>
  <div class="abs card card-teal" role="img" aria-label="White cup on a wooden table against a teal wall">
    <div class="cup"></div>
    <h3>Lorem ipsum dolor</h3>
    <p>sit amet, consectetur adipisicing elit, sed do eiusmod tempor incididunt ut labore et dolore</p>
    <div class="more">Read more <svg width="16" height="4" viewBox="0 0 16 4"><line x1="0" y1="2" x2="14" y2="2" stroke="currentColor"/><path d="M12 0 L16 2 L12 4Z" fill="currentColor"/></svg></div>
  </div>

  <div class="dash" style="left:120px;top:1021px;width:590px"></div>

  <div class="abs fcol" style="left:121px;width:120px">
    <h4>Contact Us</h4>
    <div class="contact-item" style="top:25px">
      <span class="ico"><svg width="8" height="10" viewBox="0 0 8 10"><path d="M4 0a3.5 3.5 0 0 1 3.5 3.5C7.5 6 4 10 4 10S.5 6 .5 3.5A3.5 3.5 0 0 1 4 0z" fill="#fff"/><circle cx="4" cy="3.5" r="1.3" fill="#3a150d"/></svg></span>
      <span>Lorem ipsum<br>12 Harbour Row, dolor sit<br>Road 40021</span>
    </div>
    <div class="contact-item" style="top:61px">
      <span class="ico"><svg width="7" height="10" viewBox="0 0 7 10"><rect x="0.5" y="0.5" width="6" height="9" rx="1" fill="#fff"/><rect x="1.5" y="1.5" width="4" height="5" fill="#3a150d"/></svg></span>
      <span>Call Now<br>0800-555-0199</span>
    </div>
    <div class="contact-item" style="top:90px">
      <span class="ico"><svg width="10" height="7" viewBox="0 0 10 7"><rect width="10" height="7" fill="#fff"/><path d="M0 0 L5 4 L10 0" fill="none" stroke="#3a150d"/></svg></span>
      <span>Mail Now:<br>hello@velmorebeans.com</span>
    </div>
  </div>

  <div class="abs fcol" style="left:271px">
    <h4><span class="sq"></span>Friends Page</h4>
    <div class="post" style="margin-top:8px">Lorem ipsum dolor sit amet consectetur adipisicing elit. Etiam egestas nulla sit amet<em>March 6, 2013</em></div>
    <div class="post" style="margin-top:14px">Lorem ipsum dolor sit amet consectetur adipisicing elit. Etiam egestas nulla sit amet<em>March 6, 2013</em></div>
  </div>

  <div class="abs fcol" style="left:428px">
    <h4><span class="sq"></span>Short Posts</h4>
    <div class="post" style="margin-top:8px">Lorem ipsum dolor sit amet consectetur adipisicing elit. Etiam egestas nulla sit amet<em>March 6, 2013</em></div>
    <div class="post" style="margin-top:14px">Lorem ipsum dolor sit amet consectetur adipisicing elit. Etiam egestas nulla sit amet<em>March 6, 2013</em></div>
  </div>

  <div class="abs fcol" style="left:570px;width:142px">
    <h4><svg width="14" height="10" viewBox="0 0 14 10"><rect width="14" height="10" fill="#e0353a"/><path d="M0 0 L7 6 L14 0" fill="none" stroke="#fff" stroke-width="1.2"/></svg>News Letter</h4>
    <div class="post" style="width:142px;margin-top:6px;color:var(--ink)">Lorem ipsum dolor sit amet, consectetur adipisicing elit.</div>
    <div class="field" style="margin-top:9px">Enter your Name...</div>
    <div class="field">Enter your email address...</div>
    <span class="signup">Sign Up</span>
  </div>

  <div class="abs foot">Copyright © 2013 Velmore Brothers Beans. All Rights Reserved</div>
</div>
</body>
</html>
```